American cannabis tech company business card design

Pavrel.com is seeking a modern, professional, and brand-aligned business card that represents our company and its core values: Mission, Story, Values, and Impact. As an innovative cannabis company, we want a business card that is not only visually appealing but also serves as a representation of who we are and what we stand for.

Project Scope: Design a double-sided business card that integrates our brand identity and core values. Incorporate our key brand elements, ensuring a sleek and contemporary aesthetic. Visually reflect our core values (Mission, Story, Values, Impact) in a way that is engaging yet professional.

Target Market(s)

Vendors, third parties,

Contact Information for Business Card

Contact details (name, title, email, phone, website, etc.)

Font styles to use
Other font styles liked:
• Caslon, Centra

Colors

Designer to choose colors to be used in the design.

Requirements
Must have
• Pavrel.com logo and branding A creative yet clean way to integrate our core values (Mission, Story, Values, Impact) Modern typography and a well-structured layout
Nice to have
• forest green, grey, white, black
Should not have
• references to marijuana, leafs, plants, or related product

```html
<!DOCTYPE html>
<html lang="en">
<head>
<meta charset="UTF-8">
<title>Pavrel.com Business Card</title>
<link href="https://fonts.googleapis.com/css2?family=Poppins:wght@400;500;700&display=swap" rel="stylesheet">
<style>
  :root {
    --forest: #1d3a1f;
    --ink: #1a1a1a;
    --grey: #e4e4e4;
    --paper: #ffffff;
    --muted: #444444;
  }
  * { margin: 0; padding: 0; box-sizing: border-box; }
  html, body {
    width: 1200px; height: 880px; overflow: hidden;
    background: var(--grey);
    font-family: "Poppins", sans-serif;
  }
  .stage {
    width: 1200px; height: 880px;
    display: flex; flex-direction: column; align-items: center; justify-content: center;
    gap: 40px;
  }
  .card {
    position: relative;
    width: 680px; height: 388px;
    background: var(--paper);
    border-radius: 22px;
    box-shadow: 0 6px 18px rgba(0,0,0,0.12);
    overflow: hidden;
  }
  /* Front */
  .card-front {
    display: flex; flex-direction: column; align-items: center; justify-content: center;
  }
  .brand-name {
    font-family: "Poppins", sans-serif;
    font-weight: 700;
    color: var(--forest);
    letter-spacing: 1px;
    line-height: 1;
  }
  .card-front .brand-name { font-size: 96px; }
  .front-url {
    margin-top: 34px;
    font-size: 15px;
    letter-spacing: 4px;
    color: var(--ink);
  }
  /* Back */
  .card-back .brand-name {
    position: absolute; left: 56px; top: 150px;
    font-size: 66px;
  }
  .divider {
    position: absolute; left: 360px; top: 92px;
    width: 1px; height: 118px; background: var(--ink);
  }
  .contact {
    position: absolute; left: 396px; top: 80px;
    color: var(--ink);
  }
  .contact-name {
    font-weight: 700; font-size: 19px; color: var(--forest);
    text-transform: uppercase; line-height: 1.1;
  }
  .contact-title { font-size: 13px; color: var(--muted); margin-bottom: 14px; }
  .contact-row {
    display: flex; align-items: center; gap: 10px;
    font-size: 15px; line-height: 1.45;
  }
  .contact-row svg { width: 13px; height: 13px; flex: none; fill: var(--forest); }
  .social {
    position: absolute; right: 40px; top: 232px;
    display: flex; gap: 10px;
  }
  .social-square { width: 26px; height: 26px; background: var(--forest); border-radius: 4px; }
  .values-band {
    position: absolute; left: 0; top: 300px;
    width: 430px; height: 30px;
    background: var(--forest);
    color: var(--paper);
    font-size: 15px; letter-spacing: 3px;
    display: flex; align-items: center; padding-left: 26px;
    white-space: nowrap;
  }
  .values-rule {
    position: absolute; left: 0; top: 336px;
    width: 440px; height: 2px; background: var(--forest);
  }
</style>
</head>
<body>
<main class="stage">
  <section class="card card-front">
    <div class="brand-name">PAVREL</div>
    <div class="front-url">www.PAVREL.com</div>
  </section>

  <section class="card card-back">
    <div class="brand-name">PAVREL</div>
    <div class="divider"></div>
    <div class="contact">
      <div class="contact-name">Jordan L. Hale</div>
      <div class="contact-title">Director</div>
      <div class="contact-row">
        <svg viewBox="0 0 24 24" aria-hidden="true"><path d="M6.6 10.8a15 15 0 0 0 6.6 6.6l2.2-2.2a1 1 0 0 1 1-.25 11.4 11.4 0 0 0 3.6.57 1 1 0 0 1 1 1V20a1 1 0 0 1-1 1A17 17 0 0 1 3 4a1 1 0 0 1 1-1h3.5a1 1 0 0 1 1 1c0 1.25.2 2.45.57 3.57a1 1 0 0 1-.25 1z"/></svg>
        <span>+1 555-210-4839</span>
      </div>
      <div class="contact-row">
        <svg viewBox="0 0 24 24" aria-hidden="true"><path d="M2 5h20v14H2z M2 5l10 8 10-8" stroke="#fff" stroke-width="1.5"/></svg>
        <span>team@pavrel.com</span>
      </div>
      <div class="contact-row">
        <svg viewBox="0 0 24 24" aria-hidden="true"><circle cx="12" cy="12" r="10"/><path d="M2 12h20M12 2c3 3 3 17 0 20M12 2c-3 3-3 17 0 20" stroke="#fff" stroke-width="1.2" fill="none"/></svg>
        <span>www.PAVREL.com</span>
      </div>
    </div>
    <div class="social" aria-label="Social profiles">
      <div class="social-square"></div>
      <div class="social-square"></div>
      <div class="social-square"></div>
    </div>
    <div class="values-band">Mission | Story | Values and Impact</div>
    <div class="values-rule"></div>
  </section>
</main>
</body>
</html>
```